Satchel & Sundial needs new business card design

I need a new business card design. I'm looking for out-of-the-box design which represents the freedom of being a location independent entrepreneur.
I offer coaching, retreats and trips.
I would like to see designs with and without the photo.
Colors I use are black (#000000), green (#25A796) and brown (#D7C38C)
Website satchelandsundial.example

Target Market(s)

location independent entrepreneurs, digital nomads, people looking to swap the 9 to 5 for a lifestyle business

Industry/Entity Type

Business

Contact Information for Business Card

Dorota Falkner
Your Lifestyle Business Coach, Retreat & Trip Leader
http://satchelandsundial.example
hello@satchelandsundial.example
Live a life you don't need a holiday from

Font styles to use
Serif
Sans Serif

Requirements
Must have
• One side should contain only the logo. I would also consider having the "Live a life you don't need a holiday from" on that side too (depending on how it looks)
• Please show both sides on the designs.

```html
<!DOCTYPE html>
<html lang="en">
<head>
<meta charset="utf-8">
<title>Satchel &amp; Sundial – Business Card</title>
<link rel="stylesheet" href="https://fonts.googleapis.com/css2?family=Montserrat:ital,wght@0,400;0,600;0,700;1,600&display=swap">
<style>
  :root {
    --ink: #1a1a1a;
    --black: #000000;
    --green: #25A796;
    --sand: #D7C38C;
    --sand-light: #DCCB95;
    --paper: #ffffff;
    --stage: #e9e9e9;
    --band: #1c1c1e;
  }
  * { box-sizing: border-box; margin: 0; padding: 0; }
  html, body { width: 1200px; height: 950px; overflow: hidden; }
  body {
    background: var(--stage);
    font-family: "Montserrat", Arial, sans-serif;
    color: var(--ink);
    position: relative;
  }
  .card {
    position: absolute;
    top: 140px;
    width: 380px;
    height: 665px;
    overflow: hidden;
    box-shadow: 0 10px 30px rgba(0,0,0,0.18);
  }
  /* Front side */
  .card--front { left: 170px; background: var(--sand); }
  .front__brand {
    position: absolute; top: 62px; left: 34px; right: 30px;
    font-weight: 700; font-size: 34px; line-height: 1.05;
    text-transform: uppercase; letter-spacing: 1px; color: var(--black);
    text-align: right;
  }
  .front__details { position: absolute; left: 34px; top: 345px; right: 24px; }
  .front__name {
    color: var(--green); font-weight: 600; font-size: 25px;
    text-transform: uppercase; letter-spacing: 1px; margin-bottom: 8px;
  }
  .front__role { font-size: 18px; line-height: 1.35; color: #3a352a; margin-bottom: 14px; }
  .contact { list-style: none; font-size: 17px; color: #3a352a; }
  .contact li { display: flex; align-items: center; gap: 10px; line-height: 1.6; }
  .contact svg { width: 16px; height: 16px; flex: none; }
  .front__band {
    position: absolute; left: 0; right: 0; bottom: 0; height: 118px;
    background: var(--band);
    display: flex; align-items: center; justify-content: center;
  }
  .tagline {
    color: var(--green); font-style: italic; font-weight: 600; font-size: 16px;
  }
  /* Back side */
  .card--back { left: 650px; background: var(--paper); }
  .back__pattern { position: absolute; inset: 0; }
  .back__brand {
    position: absolute; top: 50%; left: 0; right: 0;
    transform: translateY(-50%);
    text-align: center;
    font-weight: 700; font-size: 40px; line-height: 1.1;
    text-transform: uppercase; letter-spacing: 1px; color: var(--black);
  }
  .social {
    position: absolute; right: 0; bottom: 70px;
    display: flex; flex-direction: column; gap: 4px; list-style: none;
  }
  .social li { width: 22px; height: 22px; background: var(--green); }
</style>
</head>
<body>
  <section class="card card--front" aria-label="Card front">
    <div class="front__brand">Satchel &amp; Sundial</div>
    <div class="front__details">
      <h1 class="front__name">Dorota Falkner</h1>
      <p class="front__role">Your Lifestyle Business Coach<br>Retreat &amp; Trip Leader</p>
      <ul class="contact">
        <li>
          <svg viewBox="0 0 16 16" aria-hidden="true"><rect x="1" y="3" width="14" height="10" rx="1.5" fill="var(--green)"/><path d="M2 4l6 5 6-5" stroke="#fff" stroke-width="1.3" fill="none"/></svg>
          hello@satchelandsundial.example
        </li>
        <li>
          <svg viewBox="0 0 16 16" aria-hidden="true"><circle cx="8" cy="8" r="7" fill="var(--green)"/><path d="M1 8h14M8 1c3 3 3 11 0 14M8 1c-3 3-3 11 0 14" stroke="#fff" stroke-width="1" fill="none"/></svg>
          www.satchelandsundial.example
        </li>
      </ul>
    </div>
    <div class="front__band">
      <p class="tagline">Live a life you don't need a holiday from</p>
    </div>
  </section>

  <section class="card card--back" aria-label="Card back">
    <svg class="back__pattern" width="380" height="665" role="img" aria-label="Faint repeating brand-name pattern in pale grey and green">
      <defs>
        <linearGradient id="patternTone" x1="0" y1="0" x2="1" y2="1">
          <stop offset="0" stop-color="#f1f3f2"/>
          <stop offset="1" stop-color="#e7f2f0"/>
        </linearGradient>
      </defs>
      <rect width="380" height="665" fill="url(#patternTone)"/>
    </svg>
    <div class="back__brand">Satchel<br>&amp; Sundial</div>
    <ul class="social" aria-label="Social links">
      <li></li><li></li><li></li>
    </ul>
  </section>
</body>
</html>
```